Modernize Website: marcusfellwright.net

I am a novelist with an older-generation website at: marcusfellwright.net.

I am hoping to refresh this outdated website with a new, responsive redesign. I would prefer to host the code myself, and edit using Adobe Dreamweaver. So I’m not looking to use a hosted site builder like Plexo. Nor am I looking to use a CMS like Pagecraft.

In order to simplify the old site, there are a number of sections I’ll be looking to remove during this redesign. These are shown in the "MF Site Redesign" attachment. I can also provide imagery for new content (another book series in addition to the existing one), as well as higher-resolution imagery (if needed) of the old content.

Happy to answer any further questions.
Updates

I've uploaded a ZIP file containing high-res artwork associated with the new trilogy of books.

Target Market(s)

Readers of epic fantasy novels such as H.W.B. Castellane's THE WARDEN OF THE VALES, Harold P.Q. Ventris's A CROWN OF ASH AND RAIN, Victor Halloway's THE GATE OF STARS, or Dennis Vale's BLADE OF MERIVANE.

Industry/Entity Type

Entertainment

Coding

Coded - Design and coding required

Number of Pages Required

5+ page

Font styles to use
Serif
Decorative

Colors

Designer to choose colors to be used in the design.

Requirements
Must have
• I'm looking for a responsive design that displays nicely on both mobile and desktop devices. Existing site contains multiple pages, but these can obviously be combined into fewer pages (or even one) by divisions such as tabs, sections, and/or modal windows. See marcusfellwright.net for current content and "MF Site Redesign" attachment for content to be removed at this time.
Nice to have
• The ability to fulfill orders of autographed books directly from the website. I currently use Coinlo to do this, but it would be nice to incorporate a more comprehensive merchant service at a reasonable rate.
Should not have
• I'd like to host and control the site code myself. So please don't use a hosted web builder like Plexo, or a cloud-based CMS like Pagecraft.

```html
<!DOCTYPE html>
<html lang="en">
<head>
<meta charset="utf-8">
<title>Author — Marcus Fellwright</title>
<link href="https://fonts.googleapis.com/css2?family=Cinzel:wght@400;700&family=Lora:wght@400&family=Open+Sans:wght@400;600&display=swap" rel="stylesheet">
<style>
  :root{
    --bg:#0b0b0c;
    --panel:#121214;
    --red:#c4151c;
    --red-dark:#8f0d12;
    --text:#e8e6e3;
    --muted:#a9a6a2;
    --line:#2a2a2d;
  }
  *{margin:0;padding:0;box-sizing:border-box}
  html,body{width:667px;height:1200px;overflow:hidden;background:var(--bg)}
  body{position:relative;font-family:'Open Sans',sans-serif;color:var(--text)}
  .hero{position:absolute;left:0;top:0;width:667px;height:375px;
    background:linear-gradient(180deg,#2a2f38 0%,#4a4a4e 30%,#6b5240 55%,#2a1c16 85%,var(--bg) 100%)}
  .site-header{position:absolute;left:0;top:0;width:667px;height:44px;background:rgba(0,0,0,.55);display:flex;align-items:center;padding:0 24px}
  .brand{display:flex;align-items:center;gap:6px;font-family:'Cinzel',serif;font-size:13px;color:var(--text);letter-spacing:.5px}
  .brand-mark{width:8px;height:8px;background:var(--red)}
  .main-nav{margin-left:auto;display:flex;align-items:center;gap:16px;font-size:9.5px;font-weight:600;letter-spacing:.4px}
  .main-nav span{color:var(--text)}
  .login{background:var(--red);color:#fff;border-radius:10px;padding:4px 12px}
  .dropdown{position:absolute;left:452px;top:56px;width:92px;background:rgba(0,0,0,.9);font-size:9px;font-weight:600}
  .dropdown li{list-style:none;padding:5px 8px}
  .dropdown .active{background:var(--red)}
  .page-title{position:absolute;left:44px;top:168px;font-family:'Cinzel',serif;font-weight:700;font-size:62px;color:var(--red);letter-spacing:1px}
  .section-title{position:absolute;left:50px;top:410px;font-family:'Cinzel',serif;font-size:36px;color:var(--text);letter-spacing:1px}
  .photo{position:absolute;background:linear-gradient(160deg,#6d7f90 0%,#3a4552 60%,#1c2229 100%)}
  .photo-one{left:455px;top:365px;width:155px;height:215px}
  .photo-two{left:52px;top:660px;width:190px;height:178px;background:linear-gradient(160deg,#3a3a3e,#18181a)}
  .bio{position:absolute;font-family:'Lora',serif;font-size:8.6px;line-height:1.62;color:var(--muted)}
  .bio-one{left:50px;top:500px;width:395px}
  .bio-two{left:270px;top:668px;width:345px}
  .site-footer{position:absolute;left:0;top:1000px;width:667px;height:200px;text-align:center;border-top:1px solid var(--line)}
  .footer-brand{justify-content:center;margin-top:30px;font-size:14px}
  .social{display:flex;justify-content:center;gap:10px;margin-top:28px}
  .social span{width:20px;height:20px;border-radius:50%;background:var(--red)}
  .footer-nav{display:flex;justify-content:center;gap:20px;margin-top:22px;font-size:8.5px;color:var(--text)}
  .copyright{margin-top:16px;font-size:7.5px;color:var(--muted)}
</style>
</head>
<body>
  <div class="hero" role="img" aria-label="Fantasy illustration of a dragon over a rocky landscape"></div>

  <header class="site-header">
    <div class="brand"><span class="brand-mark"></span>Marcus Fellwright</div>
    <nav class="main-nav">
      <span>HOME</span><span>NOVELS ▾</span><span>WORLD ▾</span><span>AUTHOR ▾</span><span>CONTACT</span>
      <span class="login">LOGIN</span>
    </nav>
  </header>
  <ul class="dropdown">
    <li>Biography</li><li class="active">News</li><li>Events</li><li>Interviews</li><li>Q &amp; A</li>
  </ul>

  <h1 class="page-title">AUTHOR</h1>

  <h2 class="section-title">BIOGRAPHY</h2>
  <div class="photo photo-one" role="img" aria-label="Portrait photo of the author outdoors"></div>
  <p class="bio bio-one">Marcus Fellwright grew up in a quiet valley town where long winters made room for long books. He began writing at the age of nine, filling spiral notebooks with maps, kings and rivers that never ran the same way twice. By high school he had finished his first full manuscript, and by college he was studying history, myth and the craft of storytelling in earnest. After years spent teaching, editing and working odd jobs, he set out to finish the epic that had followed him since childhood. That story became the first volume of his debut series, praised by readers for its vivid worlds, honest characters and sweeping sense of adventure. Today he writes full time, dividing his days between drafting new chapters, answering reader letters and walking the hills that inspired so many of his landscapes. He still keeps the old notebooks on a shelf above his desk.</p>

  <div class="photo photo-two" role="img" aria-label="Studio portrait of the author"></div>
  <p class="bio bio-two">Fellwright is a lifelong reader of epic fantasy and a student of the old tales that shaped it. His newest trilogy returns to the world of his first novels, following a young warden who must choose between the oath she swore and the family she left behind. Between books he visits schools, libraries and conventions, speaking about world building, revision and the patience it takes to finish a long story. He lives with his wife and two dogs near the mountains, where he is already at work on the next chapter of the saga.</p>

  <footer class="site-footer">
    <div class="brand footer-brand"><span class="brand-mark"></span>Marcus Fellwright</div>
    <div class="social" aria-label="Social links"><span></span><span></span><span></span></div>
    <nav class="footer-nav"><span>Home</span><span>Novels</span><span>World</span><span>Author</span><span>Contact</span></nav>
    <p class="copyright">© Copyright 2019 Marcus Fellwright. All Rights Reserved &nbsp;|&nbsp; Terms of Use &nbsp;|&nbsp; Privacy Policy</p>
  </footer>
</body>
</html>
```